Professional and creative business card design for recruiting service providers

Our company supports German medium-sized companies in filling vacancies promptly. For this we use social media marketing and bring our customers into the visibility.

We want a professional but also creative design for our business cards.

Please look at lindqvar-staff.de to get an impression of our CI.

Target Market(s)

Small and medium-sized companies in Germany from the industry

Industry/Entity Type

Industrie, Handwerk

Contact Information for Business Card

Name, Position, Telefonnummer, Email, Website

Colors
EE7325
F08F49
F5BC92
FAE3D3
FDF4ED

Requirements
Must have
• A picture of the employee and in the style of www.lindqvar-staff.de

```html
<!DOCTYPE html>
<html lang="de">
<head>
<meta charset="utf-8">
<title>Lindqvar &amp; Staff – Visitenkarte</title>
<link rel="stylesheet" href="https://fonts.googleapis.com/css2?family=Montserrat:wght@400;500;700;800&display=swap">
<style>
  :root {
    --orange: #EE7325;
    --orange-deep: #EF5F2B;
    --ink: #1E1E1E;
    --paper: #FFFFFF;
    --stage: #C9C9C9;
    --photo-dark: #2A2C33;
    --photo-light: #E9E6E3;
  }
  * { box-sizing: border-box; margin: 0; padding: 0; }
  html, body { width: 1200px; height: 788px; overflow: hidden; }
  body {
    background: var(--stage);
    font-family: "Montserrat", sans-serif;
    display: flex;
    align-items: center;
    justify-content: center;
    gap: 40px;
  }
  .card {
    position: relative;
    width: 540px;
    height: 340px;
    border-radius: 22px;
    overflow: hidden;
  }
  /* Front */
  .card--front { background: var(--paper); }
  .card__band { position: absolute; inset: 0; }
  .card__photo {
    position: absolute;
    left: 300px; top: 28px;
    width: 215px; height: 232px;
    border-radius: 10px;
    background: linear-gradient(160deg, var(--photo-light) 0%, var(--photo-dark) 45%, var(--photo-dark) 100%);
  }
  .brand {
    position: absolute;
    left: 32px; top: 48px;
    display: flex;
    align-items: center;
    gap: 14px;
  }
  .brand__square {
    width: 44px; height: 44px;
    background: var(--orange-deep);
  }
  .brand__name {
    font-weight: 800;
    font-size: 22px;
    line-height: 1.05;
    letter-spacing: 1.5px;
    color: var(--ink);
    text-transform: uppercase;
  }
  .person {
    position: absolute;
    left: 32px; top: 128px;
  }
  .person__name {
    font-weight: 800;
    font-size: 19px;
    letter-spacing: 1px;
    color: var(--orange-deep);
    text-transform: uppercase;
  }
  .person__role {
    font-weight: 500;
    font-size: 13px;
    color: var(--ink);
    margin-top: 2px;
  }
  .contact {
    position: absolute;
    left: 32px; top: 188px;
    list-style: none;
  }
  .contact__item {
    display: flex;
    align-items: center;
    gap: 8px;
    font-size: 13px;
    color: var(--ink);
    line-height: 22px;
  }
  .contact__icon { width: 12px; height: 12px; flex: none; }
  /* Back */
  .card--back {
    background: var(--orange-deep);
    display: flex;
    align-items: center;
    justify-content: center;
    gap: 22px;
  }
  .card--back .brand__square { width: 90px; height: 90px; background: var(--paper); }
  .card--back .brand__name { color: var(--paper); font-size: 42px; letter-spacing: 4px; }
</style>
</head>
<body>

  <article class="card card--front">
    <svg class="card__band" viewBox="0 0 540 340" preserveAspectRatio="none" aria-hidden="true">
      <polygon points="0,305 540,175 540,340 0,340" fill="var(--orange-deep)"/>
    </svg>
    <div class="card__photo" role="img" aria-label="Porträtfoto des Gründers im dunklen Sakko am Schreibtisch"></div>

    <div class="brand">
      <div class="brand__square"></div>
      <div class="brand__name">Lindqvar<br>&amp; Staff</div>
    </div>

    <div class="person">
      <div class="person__name">Jonas Lindqvar</div>
      <div class="person__role">Gründer</div>
    </div>

    <ul class="contact">
      <li class="contact__item">
        <svg class="contact__icon" viewBox="0 0 12 12"><path d="M2.5 1 L4.5 1 L5.2 3.5 L4 4.5 Q5 7 7.5 8 L8.5 6.8 L11 7.5 L11 9.5 Q10.5 11 9 11 Q1 10 1 3 Q1 1.5 2.5 1Z" fill="var(--orange-deep)"/></svg>
        (123) 456 7890
      </li>
      <li class="contact__item">
        <svg class="contact__icon" viewBox="0 0 12 12"><rect x="0.5" y="2.5" width="11" height="7.5" rx="1" fill="var(--orange-deep)"/><path d="M1 3 L6 7 L11 3" stroke="#fff" stroke-width="1" fill="none"/></svg>
        info@lindqvar-staff.de
      </li>
      <li class="contact__item">
        <svg class="contact__icon" viewBox="0 0 12 12"><circle cx="6" cy="6" r="5.5" fill="var(--orange-deep)"/><path d="M0.5 6 H11.5 M6 0.5 V11.5 M6 0.5 Q2.5 6 6 11.5 M6 0.5 Q9.5 6 6 11.5" stroke="#fff" stroke-width="0.7" fill="none"/></svg>
        www.lindqvar-staff.de
      </li>
    </ul>
  </article>

  <article class="card card--back">
    <div class="brand__square"></div>
    <div class="brand__name">Lindqvar<br>&amp; Staff</div>
  </article>

</body>
</html>
```